Onlineshop for a new Golf Brand (Balls, Tees, Marker & Towels)

We are seeking a distinctive and captivating design for our online store, "Amber Falcon Golfing." The store (shopify) will focus on selling a curated selection of golf accessories, including balls, tees, markers, and towels. Given that we will have a limited product range (around 10 products), the design should emphasize individual product detail and the brand's ethos. We place a high emphasis on an intuitive user experience and a design that resonates with the values and aesthetics of our brand.

Design & Aesthetics:

Style Direction: Minimalistic with a touch of luxury. The design should accentuate the premium nature and quality of our products.
Color Scheme: Primary colors should be aligned with our brand logo and the provided design assets. We prefer a mix of calm and neutral shades, complemented by purposeful accents that draw attention to specific areas.
Typography: A contemporary, clear, and legible typeface suitable for both headlines and body text. Typography should complement the overall design aesthetic without overshadowing it.
Imagery: With a limited product range, product images should be the centerpiece. They should be large, clearly visible, with the option to zoom in for a closer look at details. Incorporating additional lifestyle shots showcasing the products in action can enhance the shopping experience.
UI/UX Elements: Clear and distinguishable call-to-action buttons, intuitive navigation elements, and understandable icons. The checkout process should be streamlined and swift, ensuring customers have a frictionless experience.

I added some mockups of the balls and their packaging as well as the main logo (Falcon) and the alternative one (letters).

```html
<!DOCTYPE html>
<html lang="en">
<head>
<meta charset="utf-8">
<title>Amber Falcon Golfing</title>
<link rel="stylesheet" href="https://fonts.googleapis.com/css2?family=Antonio:wght@400;600&family=Poppins:wght@400;500;600&display=swap">
<style>
  :root{
    --brand:#870a0a;
    --ink:#1d1d1d;
    --muted:#555;
    --paper:#ffffff;
    --stone:#ececec;
    --slate:#4a4a4a;
    --line:#dcdcdc;
  }
  *{box-sizing:border-box;margin:0;padding:0}
  html,body{width:1200px;height:5372px;overflow:hidden}
  body{position:relative;background:var(--paper);font-family:"Poppins",sans-serif;color:var(--ink)}
  .abs{position:absolute}
  .display{font-family:"Antonio",sans-serif;font-weight:600;letter-spacing:.2px}
  .photo{position:absolute}

  .announcement{left:0;top:0;width:1200px;height:42px;background:var(--brand);color:#fff;
    font-size:13px;font-weight:600;text-transform:uppercase;text-align:center;line-height:42px;letter-spacing:.3px}
  .brand-mark{left:0;top:150px;width:1200px;text-align:center;color:var(--brand);font-size:34px;font-weight:600;line-height:1.1}
  .brand-mark small{display:block;font-size:20px;font-weight:600;margin-top:6px}
  .cart{left:1062px;top:172px}
  .main-nav{left:0;top:259px;width:1200px;display:flex;justify-content:center;gap:44px;font-size:13px;font-weight:500;text-transform:uppercase}

  .hero-title{left:0;top:302px;width:1200px;text-align:center;font-size:40px;white-space:nowrap}
  .hero-photo{left:111px;top:363px;width:977px;height:422px;background:radial-gradient(ellipse at 50% 55%,#f3f3f3,#dcdcdc)}
  .slider-bar{left:111px;top:785px;width:977px;height:37px;border:1px solid var(--line);border-top:none;
    display:flex;align-items:center;justify-content:center;gap:22px;font-size:13px;color:var(--muted)}
  .dot{width:8px;height:8px;border-radius:50%;border:1px solid #999}
  .dot.active{background:#1d2b4a;border-color:#1d2b4a}

  .section-title{left:0;width:1200px;text-align:center;font-size:40px}
  .card{position:absolute;width:309px;height:338px}
  .card.framed{border:1px solid #cfcfcf}
  .card-name{position:absolute;width:309px;text-align:center;font-size:20px;font-weight:500}
  .card-sub{position:absolute;width:309px;text-align:center;font-size:15px;color:var(--muted)}
  .card-price{position:absolute;width:309px;text-align:center;font-size:22px;font-weight:600}

  .promo-red{background:var(--brand);color:#fff}
  .promo-text{font-size:33px;line-height:1.17;font-weight:600;white-space:nowrap}
  .promo-text.narrow{font-size:31px}
  .btn-light{display:inline-block;background:#fff;color:var(--ink);border-radius:22px;font-size:12px;font-weight:500;
    padding:11px 29px;text-transform:uppercase;margin-top:22px}

  .popular{left:0;top:3093px;width:1200px;height:1425px;background:var(--brand);color:#fff}
  .tile{position:absolute;width:448px;height:480px;background:linear-gradient(135deg,#f2f3f1,#e6e8e5)}
  .tile .inner{position:absolute;left:116px;top:93px;width:216px;height:272px;box-shadow:0 4px 10px rgba(0,0,0,.15)}
  .tile-caption{position:absolute;width:448px;text-align:center;font-size:22px}

  .subscribe-title{left:0;top:4588px;width:1200px;text-align:center;font-size:40px}
  .subscribe-sub{left:0;top:4644px;width:1200px;text-align:center;font-size:15px;color:#333}
  .field{position:absolute;height:50px;border:1px solid #bbb;background:#fff;font-size:15px;padding-left:20px;
    display:flex;align-items:center;justify-content:space-between;padding-right:18px;box-shadow:0 1px 3px rgba(0,0,0,.08)}

  .footer{left:0;top:4817px;width:1200px;height:555px;background:var(--stone)}
  .footer h4{font-family:"Antonio",sans-serif;font-weight:600;font-size:26px;margin-bottom:12px}
  .footer ul{list-style:none;font-size:12px;line-height:21px;color:#333}
  .footer-logo{display:flex;align-items:center;justify-content:center;text-align:center;border:3px solid var(--brand);
    border-radius:14px;color:var(--brand);font-size:18px;font-weight:600;line-height:1.2;background:#fff}
  .pay{display:flex;gap:14px}
  .pay span{width:38px;height:22px;border-radius:3px;background:#fff;border:1px solid #ccc}
</style>
</head>
<body>

<div class="abs announcement">Perspiciatis unde omnis iste natus error sit voluptatem accusantium doloremque laudantium</div>

<div class="abs brand-mark">Amber Falcon<small>Golfing</small></div>
<svg class="abs cart" width="26" height="28" viewBox="0 0 26 28" fill="none" stroke="#1d2b4a" stroke-width="2"><rect x="3" y="8" width="20" height="17" rx="2"/><path d="M8 12v-4a5 5 0 0 1 10 0v4"/></svg>
<nav class="abs main-nav"><span>Home</span><span>About</span><span>Services</span><span>Products</span><span>Blog</span></nav>

<h1 class="abs hero-title display">Amber Falcon for the Seafood Lover in You.</h1>
<div class="photo hero-photo" role="img" aria-label="White ball tube and round marker tin with red band on a grey backdrop"></div>
<div class="abs slider-bar"><span>‹</span><span class="dot"></span><span class="dot"></span><span class="dot active"></span><span>›</span><span>❙❙</span></div>

<h2 class="abs section-title display" style="top:892px">Our Products</h2>
<div class="card photo" style="left:111px;top:970px;background:linear-gradient(180deg,#efc9cf,#e7b9c0)" role="img" aria-label="Model wearing a white brand T-shirt on a pink background"></div>
<div class="card photo" style="left:445px;top:970px;background:radial-gradient(ellipse at 50% 50%,#e4e4e4,#f4f4f4)" role="img" aria-label="Folded white golf towel with brand print"></div>
<div class="card photo" style="left:779px;top:970px;background:linear-gradient(180deg,#8aa05a,#3f5a2a)" role="img" aria-label="Golf bag with clubs standing on a green course"></div>
<div class="card-name" style="left:111px;top:1315px">Jsieuas Namse</div><div class="card-sub" style="left:111px;top:1342px">Kaseiks Saesien</div><div class="card-price" style="left:111px;top:1374px">$50.00 USD</div>
<div class="card-name" style="left:445px;top:1315px">Iasoej Eaisen</div><div class="card-sub" style="left:445px;top:1342px">Kaseiks Saesien</div><div class="card-price" style="left:445px;top:1374px">$50.00 USD</div>
<div class="card-name" style="left:779px;top:1315px">Oseses Rasems</div><div class="card-sub" style="left:779px;top:1342px">Kaseiks Saesien</div><div class="card-price" style="left:779px;top:1374px">$50.00 USD</div>

<div class="abs promo-red" style="left:111px;top:1486px;width:599px;height:336px;padding:124px 0 0 54px">
  <p class="display promo-text">Neque porro quisquam estqui dolorem<br>ipsum quia dolorsitametc onsectetur</p>
</div>
<div class="photo" style="left:710px;top:1486px;width:378px;height:336px;background:radial-gradient(circle at 50% 48%,#f4f4f4 0 120px,var(--slate) 122px)" role="img" aria-label="White golf ball with brand print on a dark grey background"></div>
<div class="photo" style="left:111px;top:1822px;width:599px;height:620px;background:linear-gradient(180deg,#e3e3e3,#d4d4d4)" role="img" aria-label="White ball tube with red band beside a black drawstring pouch"></div>
<div class="abs promo-red" style="left:710px;top:1822px;width:378px;height:620px;padding:372px 0 0 20px">
  <p class="display promo-text narrow">Perspiciatis unde omnis iste<br>natuser rorsit</p>
  <span class="btn-light">Learn more</span>
</div>

<h2 class="abs section-title display" style="top:2508px">New Products</h2>
<div class="card framed photo" style="left:111px;top:2588px;background:radial-gradient(circle at 50% 50%,#f2f2f2 0 112px,#fff 114px)" role="img" aria-label="White golf ball with lettermark print"></div>
<div class="card photo" style="left:445px;top:2588px;background:linear-gradient(180deg,#7d97ad,#5d7890)" role="img" aria-label="Model wearing a navy brand T-shirt on a blue background"></div>
<div class="card framed photo" style="left:779px;top:2588px;background:#fafafa" role="img" aria-label="Black and white golf bag with clubs and balls"></div>
<div class="card-name" style="left:111px;top:2932px">Jsieuas Namse</div><div class="card-sub" style="left:111px;top:2959px">Kaseiks Saesien</div><div class="card-price" style="left:111px;top:2990px">$50.00 USD</div>
<div class="card-name" style="left:445px;top:2932px">Iasoej Eaisen</div><div class="card-sub" style="left:445px;top:2959px">Kaseiks Saesien</div><div class="card-price" style="left:445px;top:2990px">$50.00 USD</div>
<div class="card-name" style="left:779px;top:2932px">Oseses Rasems</div><div class="card-sub" style="left:779px;top:2959px">Kaseiks Saesien</div><div class="card-price" style="left:779px;top:2990px">$50.00 USD</div>

<section class="abs popular">
  <p class="abs display" style="left:0;top:80px;width:1200px;text-align:center;font-size:22px">Popular Products</p>
  <h2 class="abs display" style="left:0;top:124px;width:1200px;text-align:center;font-size:35px;line-height:1.1">Quisquam estqui doloreipsum quia dolorsit<br>hametc onsectetur</h2>
  <div class="tile" style="left:111px;top:242px"><div class="inner photo" style="background:#e6e6e6" role="img" aria-label="Framed print of ball tube and marker tin"></div></div>
  <div class="tile" style="left:640px;top:242px"><div class="inner photo" style="background:linear-gradient(180deg,#f0c4cc,#e8b7c0)" role="img" aria-label="Framed print of a model in a white brand T-shirt"></div></div>
  <p class="tile-caption display" style="left:111px;top:735px">Haequuntur Magnidolores</p>
  <p class="tile-caption display" style="left:640px;top:735px">Haequuntur Magnidolores</p>
  <div class="tile" style="left:111px;top:822px"><div class="inner photo" style="background:linear-gradient(180deg,#d8c58a,#8a6e2e)" role="img" aria-label="Framed print of a golf bag with clubs at sunset"></div></div>
  <div class="tile" style="left:640px;top:822px"><div class="inner photo" style="background:#e2e2e2" role="img" aria-label="Framed print of ball tube and black pouch"></div></div>
  <p class="tile-caption display" style="left:111px;top:1315px">Haequuntur Magnidolores</p>
  <p class="tile-caption display" style="left:640px;top:1315px">Haequuntur Magnidolores</p>
</section>

<h2 class="abs subscribe-title display">Be the first to know</h2>
<p class="abs subscribe-sub">Join our email list to learn about exclusive showings and new collections.</p>
<div class="field" style="left:372px;top:4683px;width:404px">Email <span>→</span></div>

<footer class="abs footer">
  <div class="abs" style="left:111px;top:70px"><h4>Quick Links</h4><ul><li>Home</li><li>About</li><li>Services</li><li>Products</li><li>Blog</li><li>Contact Us</li></ul></div>
  <div class="abs" style="left:317px;top:70px"><h4>Links</h4><ul><li>Copyright</li><li>Legal</li><li>Privacy</li><li>Accessibility</li><li>Sitemap</li></ul></div>
  <div class="abs footer-logo" style="left:755px;top:60px;width:118px;height:138px">Amber<br>Falcon<br>Golfing</div>
  <div class="abs" style="left:925px;top:70px;width:170px"><h4>Our Mission</h4><ul><li style="line-height:17px">Saerspiciatis unde omnis iste natus error sit voluptatem.</li></ul></div>
  <h4 class="abs" style="left:111px;top:272px">Subscribe to our emails</h4>
  <div class="field" style="left:111px;top:321px;width:404px">Email <span>→</span></div>
  <div class="abs" style="left:111px;top:421px;width:977px;height:1px;background:#cfcfcf"></div>
  <div class="abs pay" style="left:434px;top:456px"><span></span><span></span><span></span><span></span><span></span><span></span></div>
  <p class="abs" style="left:0;top:504px;width:1200px;text-align:center;font-size:11px;color:#555">©2023. All rights reserved.</p>
</footer>

</body>
</html>
```